2 Page Web Design Project (coded)

What does the company do?
Pilot contracting, flying private/corporate jets.

What is its target market?
The target market is primarily the private jet management market, i.e. companies, which specialize in private aircraft management and are looking to fill crew positions on a short/long term basis, usually on short notice basis

How many pages should your website include?
2 Pages: 1/ Front Page with Company Logo, 2/ Services and Contact page

Do you want coding included? YES

Do you have any style you would like your website to have?
The main colors of my logo should be kept. Please see attached business card logo.

Other Instructions: Please see Veltraxa's website (media section) for Skyrunner 812 pictures for free download, which can be incorporated into the website. Link: http://www.veltraxa.example/en/aerospace/media-centre/multimedia-library/details?categoryID=L3-Veltraxa%20Skyrunner%20812%20Aircraft.

Please see www.midairstaffingdesk.example for services description.
Find attached source file business card and use loge design/font for website, so both business card and website are consistent.

Requirements
Must have
• email link to link to my personal email, without giving my email address.

```html
<!DOCTYPE html>
<html lang="en">
<head>
<meta charset="utf-8">
<title>Halcyon Crew Leasing</title>
<link href="https://fonts.googleapis.com/css2?family=Roboto+Condensed:wght@400&family=Arimo:wght@400&display=swap" rel="stylesheet">
<style>
  :root {
    --page-bg: #ffffff;
    --brand-brown: #4a3418;
    --brand-dark: #3a2612;
    --brand-circle: #5e3f1e;
    --text-main: #222222;
    --text-muted: #777777;
    --nav-bg: #e6e7e8;
    --nav-border: #3c3c3c;
    --frame-bg: #f7f7f7;
    --frame-border: #e3e3e3;
    --rule: #bcbcbc;
    --dot: #8a8a8a;
  }
  * { margin: 0; padding: 0; box-sizing: border-box; }
  html, body { width: 1200px; height: 862px; overflow: hidden; background: var(--page-bg); }
  .page { position: relative; width: 1200px; height: 862px; font-family: "Arimo", Arial, sans-serif; color: var(--text-main); }

  .brand { position: absolute; left: 202px; top: 8px; width: 400px; height: 128px; text-decoration: none; }
  .brand-mark { position: absolute; left: 0; top: 0; width: 126px; height: 126px; border-radius: 50%;
    background: var(--brand-circle); box-shadow: 0 2px 3px rgba(0,0,0,.25); }
  .brand-name { position: absolute; left: 130px; top: 42px; width: 266px; text-align: center;
    font-family: "Roboto Condensed", sans-serif; font-weight: 400; font-size: 26px; line-height: 28px;
    letter-spacing: 1px; color: var(--brand-dark); }
  .brand-name span { display: block; }

  .main-nav { position: absolute; left: 609px; top: 58px; width: 386px; height: 36px;
    background: linear-gradient(to right, rgba(230,231,232,0) 0, var(--nav-bg) 40px);
    border: 1px dashed var(--nav-border); border-left: none; box-shadow: 2px 2px 3px rgba(0,0,0,.12); }
  .main-nav a { position: absolute; top: 9px; font-family: "Roboto Condensed", sans-serif; font-size: 16px;
    color: var(--text-main); text-decoration: none; letter-spacing: .2px; }
  .nav-home { left: 76px; } .nav-services { left: 150px; } .nav-contact { left: 281px; }

  .hero-glow { position: absolute; left: 150px; top: 300px; width: 900px; height: 190px;
    background: radial-gradient(ellipse at center, rgba(0,0,0,.12) 0, rgba(0,0,0,0) 65%); }
  .hero-frame { position: absolute; left: 204px; top: 141px; width: 793px; height: 323px;
    background: var(--frame-bg); border: 1px solid var(--frame-border); box-shadow: 0 3px 4px rgba(0,0,0,.18); }
  .hero-photo { position: absolute; left: 13px; top: 13px; width: 765px; height: 296px;
    background: linear-gradient(180deg, #d2d3d7 0%, #c9cbd1 45%, #e9eaec 75%, #f1f1f2 100%); }
  .slider-dots { position: absolute; left: 582px; top: 480px; display: flex; gap: 3px; }
  .slider-dots span { width: 9px; height: 9px; border-radius: 50%; background: var(--dot); box-shadow: inset 0 1px 1px rgba(0,0,0,.3); }

  .section-title { position: absolute; left: 203px; font-family: "Roboto Condensed", sans-serif;
    font-weight: 400; font-size: 16.5px; color: var(--text-main); }
  .welcome-title { top: 505px; width: 797px; padding-bottom: 7px; border-bottom: 1px dotted var(--rule); }
  .welcome-text { position: absolute; left: 203px; top: 545px; width: 805px; font-size: 12.3px; line-height: 19.7px; }
  .welcome-text p + p { margin-top: 19.7px; }
  .services-title { top: 681px; }

  .service-list { list-style: none; }
  .service-list li { position: absolute; font-family: "Roboto Condensed", sans-serif; font-size: 14px; color: var(--brand-brown); padding-left: 15px; }
  .service-list li::before { content: "→"; position: absolute; left: 0; top: 3px; font-size: 9px; color: #555; }
  .svc-1 { left: 217px; top: 705px; } .svc-2 { left: 424px; top: 706px; } .svc-3 { left: 677px; top: 705px; }
  .svc-4 { left: 217px; top: 743px; } .svc-5 { left: 424px; top: 744px; }

  .site-footer { position: absolute; left: 0; top: 804px; width: 1200px; border-top: 1px solid #d0d0d0;
    text-align: center; padding-top: 24px; font-size: 11.5px; color: var(--text-muted); }
</style>
</head>
<body>
<div class="page">
  <a class="brand" href="#home">
    <span class="brand-mark"></span>
    <span class="brand-name"><span>HALCYON CREW</span><span>LEASING</span></span>
  </a>

  <nav class="main-nav">
    <a class="nav-home" href="#home">HOME</a>
    <a class="nav-services" href="#services">OUR SERVICES</a>
    <a class="nav-contact" href="#contact">CONTACT US</a>
  </nav>

  <div class="hero-glow"></div>
  <div class="hero-frame">
    <div class="hero-photo" role="img" aria-label="Photo of a white business jet with a blue tail parked on a snowy apron, with a faint world map overlay"></div>
  </div>
  <div class="slider-dots"><span></span><span></span><span></span></div>

  <h2 class="section-title welcome-title">Welcome</h2>
  <div class="welcome-text">
    <p>Halcyon Crew Leasing is a service provider to the Business Aviation community, providing qualified pilots for aircraft owners and operators, flying the Veltraxa Skyrunner series of aircraft.</p>
    <p>At Halcyon Crew Leasing we exclusively focus on the needs of the Business Aviation market and it’s discerning clients. We demand the best of our crew, who are tasked in providing short/long term crewing. All our crews have multiple years experience in the VVIP market, are highly qualified and come from various backgrounds including Military, Airline and Instruction.</p>
  </div>

  <h2 class="section-title services-title">What we do</h2>
  <ul class="service-list">
    <li class="svc-1">Short notice crewing</li>
    <li class="svc-2">Short term/long term crewing</li>
    <li class="svc-3">Permanent crew placement/hiring support</li>
    <li class="svc-4">Aircraft ferry</li>
    <li class="svc-5">New/pre-owned aircraft delivery</li>
  </ul>

  <footer class="site-footer">© Halcyon crew 2012. All Rights Reserved</footer>
</div>
</body>
</html>
```